Quorvix banner ad for roofing company

We need an ad created for a Quorvix banner advertising campaign for a UK based roofing company.

The design should have a large photograph on the background (see attached).
The design should have our Glimmerdew rating (5 stars).
There should be a large text header at the top which reads "Your local roofing experts"

The following services should be listed:
- New roofs
- General roof repairs
- Drone surveys
- Single ply roofing
- Steel cladding
- Asbestos removal

The company logo needs to be visible (attached). Also the company telephone number 020 7946 0321 and website www.brinthoveroofing.com

The advert needs to be horizontal/landscape design. For full spec, please see here: https://promo.quorvix.com/advertiser-help/guides/ad-formats/single-photo-ads

Size required: 1.91:1 - 1200 x 628 pixels

```html
<!DOCTYPE html>
<html lang="en">
<head>
<meta charset="utf-8">
<title>Brinthove Roofing – Your Local Roofing Experts</title>
<link rel="stylesheet" href="https://fonts.googleapis.com/css2?family=Montserrat:wght@300;400;500;600;700&display=swap">
<style>
  :root {
    --navy: #1b3f6c;
    --sky: #2aa8df;
    --white: #ffffff;
    --rating-green: #00b67a;
    --photo-a: #6f8a5c;
    --photo-b: #9aa39a;
    --photo-c: #c9b6a0;
  }
  * { margin: 0; padding: 0; box-sizing: border-box; }
  html, body { width: 1200px; height: 628px; overflow: hidden; background: var(--white); }
  .ad {
    position: relative; width: 1200px; height: 628px; overflow: hidden;
    font-family: 'Montserrat', sans-serif; color: var(--white);
  }
  .ad svg.backdrop { position: absolute; inset: 0; }
  .brand {
    position: absolute; left: 50px; top: 38px;
    display: flex; align-items: center; gap: 10px;
    font-size: 32px; font-weight: 700; color: var(--sky); letter-spacing: -0.5px;
  }
  .brand-dot { width: 34px; height: 34px; border-radius: 50%; background: var(--white); }
  .headline { position: absolute; left: 50px; top: 118px; line-height: 1; }
  .headline .lead { display: block; font-size: 44px; font-weight: 300; margin-bottom: 18px; }
  .headline .strong { display: block; font-size: 64px; font-weight: 700; margin-bottom: 6px; letter-spacing: -0.5px; }
  .rule { position: absolute; left: 55px; top: 329px; width: 400px; height: 2px; background: var(--white); }
  .services { position: absolute; left: 58px; top: 361px; list-style: none; }
  .services li {
    display: flex; align-items: center; gap: 14px;
    font-size: 21px; font-weight: 500; height: 37px;
  }
  .services svg { width: 18px; height: 18px; }
  .rating { position: absolute; left: 340px; top: 517px; }
  .rating-note { font-size: 13px; font-weight: 500; margin-bottom: 8px; }
  .rating-name { font-size: 17px; font-weight: 500; margin-bottom: 4px; }
  .rating-bar { width: 105px; height: 18px; background: var(--rating-green); }
  .contact {
    position: absolute; top: 532px; display: flex; align-items: center; gap: 14px;
  }
  .contact-icon {
    width: 46px; height: 46px; border-radius: 50%; background: var(--white);
    display: flex; align-items: center; justify-content: center; flex: none;
  }
  .contact-label { font-size: 15px; font-weight: 500; line-height: 1.2; }
  .contact-value { font-size: 22px; font-weight: 700; line-height: 1.2; white-space: nowrap; }
  .contact-phone { left: 576px; }
  .contact-web { left: 858px; }
  .contact-web .contact-value { font-size: 18px; font-weight: 600; }
</style>
</head>
<body>
<main class="ad">
  <svg class="backdrop" width="1200" height="628" viewBox="0 0 1200 628">
    <defs>
      <linearGradient id="photoTone" x1="0" y1="0" x2="1" y2="1">
        <stop offset="0" stop-color="#6f8a5c"/>
        <stop offset="0.55" stop-color="#9aa39a"/>
        <stop offset="1" stop-color="#c9b6a0"/>
      </linearGradient>
    </defs>
    <rect x="400" y="0" width="800" height="628" fill="url(#photoTone)" role="img" aria-label="Aerial drone photograph of a residential block estate with pale grey metal roofs, green courtyards, roads and a car park"/>
    <path d="M0 0 H442 C420 210 450 420 560 515 L720 628 H0 Z" fill="#1b3f6c"/>
    <path d="M442 0 C420 210 450 420 560 515 L720 628" fill="none" stroke="#2aa8df" stroke-width="7"/>
    <path d="M508 512 H1200 V600 H560 Z" fill="#2aa8df"/>
  </svg>

  <div class="brand"><span class="brand-dot"></span>brinthoveroofing</div>

  <h1 class="headline">
    <span class="lead">Your Local</span>
    <span class="strong">Roofing</span>
    <span class="strong">Experts</span>
  </h1>
  <div class="rule"></div>

  <ul class="services">
    <li><svg viewBox="0 0 18 18"><path d="M2 9.5 L7 14 L16 3" fill="none" stroke="#fff" stroke-width="2.6"/></svg>New roofs</li>
    <li><svg viewBox="0 0 18 18"><path d="M2 9.5 L7 14 L16 3" fill="none" stroke="#fff" stroke-width="2.6"/></svg>General roof repairs</li>
    <li><svg viewBox="0 0 18 18"><path d="M2 9.5 L7 14 L16 3" fill="none" stroke="#fff" stroke-width="2.6"/></svg>Drone surveys</li>
    <li><svg viewBox="0 0 18 18"><path d="M2 9.5 L7 14 L16 3" fill="none" stroke="#fff" stroke-width="2.6"/></svg>Single ply roofing</li>
    <li><svg viewBox="0 0 18 18"><path d="M2 9.5 L7 14 L16 3" fill="none" stroke="#fff" stroke-width="2.6"/></svg>Steel cladding</li>
    <li><svg viewBox="0 0 18 18"><path d="M2 9.5 L7 14 L16 3" fill="none" stroke="#fff" stroke-width="2.6"/></svg>Asbestos removal</li>
  </ul>

  <div class="rating">
    <p class="rating-note">39/5 star reviews</p>
    <p class="rating-name">Glimmerdew</p>
    <div class="rating-bar" role="img" aria-label="Five star rating"></div>
  </div>

  <div class="contact contact-phone">
    <span class="contact-icon">
      <svg width="26" height="26" viewBox="0 0 24 24"><path d="M6.6 10.8a15 15 0 0 0 6.6 6.6l2.2-2.2a1 1 0 0 1 1-.25 11.4 11.4 0 0 0 3.6.57 1 1 0 0 1 1 1V20a1 1 0 0 1-1 1A17 17 0 0 1 3 4a1 1 0 0 1 1-1h3.5a1 1 0 0 1 1 1c0 1.25.2 2.45.57 3.57a1 1 0 0 1-.25 1z" fill="#1b3f6c"/></svg>
    </span>
    <div>
      <p class="contact-label">Call us on</p>
      <p class="contact-value">020 7946 0321</p>
    </div>
  </div>

  <div class="contact contact-web">
    <span class="contact-icon">
      <svg width="28" height="28" viewBox="0 0 24 24" fill="none" stroke="#1b3f6c" stroke-width="1.8"><circle cx="12" cy="12" r="9.5"/><ellipse cx="12" cy="12" rx="4" ry="9.5"/><path d="M2.5 12h19M4 7h16M4 17h16"/></svg>
    </span>
    <div>
      <p class="contact-label">Visit the site</p>
      <p class="contact-value">www.brinthoveroofing.com</p>
    </div>
  </div>
</main>
</body>
</html>
```